Harborlight Amusement Collective (HAC)

We need a business card design for Harborlight Amusement Collective. Modern and sleek looking, with all critical information. Open to single or double sided designs, if double sided info needs to be all on one side. The main Logo is Harborlight Amusement collective and must be on the card. The other three logos are for the brands that fall under the group, they might be good on the back.

Industry/Entity Type

Business

```html
<!DOCTYPE html>
<html lang="en">
<head>
<meta charset="utf-8">
<title>Harborlight Amusement Collective – Business Card</title>
<link href="https://fonts.googleapis.com/css2?family=Montserrat:wght@400;500;600;700&family=Fira+Sans+Condensed:wght@600&display=swap" rel="stylesheet">
<style>
  :root {
    --backdrop: #3a3a3c;
    --card: #1d1d1f;
    --strip: #ffffff;
    --blue: #2457a4;
    --green: #8fb335;
    --white: #ffffff;
    --muted: #c9ccd3;
    --emboss: #2c2c2f;
    --divider: #9a9a9a;
  }
  * { margin: 0; padding: 0; box-sizing: border-box; }
  html, body { width: 799px; height: 1200px; overflow: hidden; }
  body {
    background: var(--backdrop);
    font-family: "Montserrat", sans-serif;
    position: relative;
  }
  .card {
    position: absolute;
    left: 80px;
    width: 640px;
    height: 366px;
    background: var(--card);
    border-radius: 4px;
    overflow: hidden;
    box-shadow: 0 10px 24px rgba(0,0,0,.45);
  }
  .card--front { top: 150px; }
  .card--back { top: 690px; }

  /* Front */
  .front-mark {
    position: absolute;
    top: 95px; left: 0; width: 100%;
    text-align: center;
    color: var(--emboss);
    font-weight: 700;
    font-size: 30px;
    letter-spacing: 2px;
    line-height: 1.25;
    text-transform: uppercase;
  }
  .brand-strip {
    position: absolute;
    left: 0; bottom: 0;
    width: 100%; height: 96px;
    background: var(--strip);
    display: flex;
    align-items: center;
    justify-content: space-around;
    padding: 0 18px;
  }
  .brand {
    display: flex;
    align-items: center;
    gap: 8px;
    font-weight: 700;
    font-size: 19px;
  }
  .brand__dot { width: 16px; height: 16px; border-radius: 50%; }
  .brand--tickets { color: var(--green); }
  .brand--tickets .brand__dot { background: var(--green); }
  .brand--hospitality { color: #1d1d1f; }
  .brand--gate { color: var(--blue); }
  .brand--gate .brand__dot { background: var(--blue); }
  .brand-divider { width: 1px; height: 46px; background: var(--divider); }

  /* Back */
  .back-shapes { position: absolute; inset: 0; }
  .wordmark {
    position: absolute;
    top: 20px; left: 40px; right: 40px;
    color: var(--green);
    font-weight: 600;
    text-transform: uppercase;
  }
  .wordmark__top {
    text-align: center;
    font-size: 25px;
    letter-spacing: 1px;
    line-height: 32px;
  }
  .wordmark__bottom {
    display: flex;
    align-items: center;
    gap: 18px;
    margin-top: 4px;
    font-size: 20px;
    letter-spacing: 9px;
    line-height: 28px;
  }
  .wordmark__rule {
    flex: 1;
    height: 3px;
    background: var(--blue);
  }
  .contact {
    position: absolute;
    top: 114px; left: 34px;
    color: var(--white);
  }
  .contact__name {
    font-family: "Fira Sans Condensed", sans-serif;
    font-weight: 600;
    font-size: 28px;
    line-height: 1.05;
  }
  .contact__role { font-size: 14px; margin-bottom: 12px; color: var(--muted); }
  .contact__list { list-style: none; font-size: 14px; line-height: 23px; }
  .contact__list li { display: flex; align-items: center; gap: 10px; }
  .contact__list svg { width: 13px; height: 13px; fill: var(--white); }
  .address {
    position: absolute;
    left: 34px; bottom: 26px;
    color: var(--white);
    font-size: 14px;
    letter-spacing: .4px;
  }
  .band-mark {
    position: absolute;
    right: 58px; top: 222px;
    color: var(--white);
    font-weight: 700;
    font-size: 44px;
    letter-spacing: 4px;
  }
</style>
</head>
<body>

<section class="card card--front" aria-label="Card front">
  <div class="front-mark">Harborlight<br>Amusement<br>Collective</div>
  <div class="brand-strip">
    <div class="brand brand--tickets"><span class="brand__dot"></span>Bayline Tickets</div>
    <span class="brand-divider"></span>
    <div class="brand brand--hospitality">Tierside Hospitality</div>
    <span class="brand-divider"></span>
    <div class="brand brand--gate"><span class="brand__dot"></span>gatewise.com.au</div>
  </div>
</section>

<section class="card card--back" aria-label="Card back">
  <svg class="back-shapes" width="640" height="366" viewBox="0 0 640 366" aria-hidden="true">
    <polygon points="0,100 410,100 640,250 640,300 380,300 300,250 0,250" fill="var(--blue)"/>
  </svg>
  <div class="wordmark">
    <div class="wordmark__top">Harborlight Amusement</div>
    <div class="wordmark__bottom">
      <span class="wordmark__rule"></span>
      <span>Collective</span>
      <span class="wordmark__rule"></span>
    </div>
  </div>
  <div class="contact">
    <div class="contact__name">Jordan Lee Carter</div>
    <div class="contact__role">Managing Director</div>
    <ul class="contact__list">
      <li><svg viewBox="0 0 16 16"><path d="M3 1l3 3-2 2c1 2 3 4 5 5l2-2 3 3-2 3C6 14 2 10 1 3z"/></svg>555.555.5555</li>
      <li><svg viewBox="0 0 16 16"><path d="M1 3h14v10H1z M2 4l6 5 6-5" fill="none" stroke="#fff" stroke-width="1.5"/></svg>jordan@harborlightac.com</li>
      <li><svg viewBox="0 0 16 16"><circle cx="8" cy="8" r="6.5" fill="none" stroke="#fff" stroke-width="1.5"/><path d="M1.5 8h13M8 1.5c-3 3-3 10 0 13M8 1.5c3 3 3 10 0 13" fill="none" stroke="#fff" stroke-width="1.2"/></svg>www.harborlightac.com</li>
    </ul>
  </div>
  <div class="band-mark">HAC</div>
  <div class="address">18 Pier Row, Bayview City, US 204816</div>
</section>

</body>
</html>
```